Coffee and Plastics

I am looking for a completely new site that shows the products we have. Our current site is www.velmorebrothersbeans.com. We are open minded to what designers come up with. Our current site is www.velmorebrothersbeans.com. You can you the information from there to start the site. I need these tabs on the main home page. ( Home, Coffee & Tea, Condiments, and Paper and Plastics, and Contact.) You can take photos and info from my Current site. In products page.
I will be uploading info and photo for paper and plastics.
Look and feel
Each slider illustrates characteristics of the customer's brand and the style your logo design should communicate.

```html
<!DOCTYPE html>
<html lang="en">
<head>
<meta charset="utf-8">
<title>Velmore Brothers Beans</title>
<link rel="stylesheet" href="https://fonts.googleapis.com/css2?family=Lato:ital,wght@0,300;0,400;0,700;1,300&display=swap">
<style>
  :root {
    --page: #ffffff;
    --ink: #5a2a1e;
    --ink-soft: #6b3a2a;
    --accent: #b07a58;
    --band: #5c2116;
    --band-text: #ffffff;
    --bean-dark: #4a2417;
    --bean-mid: #7a4a33;
  }
  html, body { margin: 0; padding: 0; overflow: hidden; }
  body { width: 765px; height: 1200px; position: relative; background: var(--page); font-family: "Lato", sans-serif; color: var(--ink); }

  .site-nav { position: absolute; top: 57px; right: 21px; display: flex; gap: 23px; font-size: 12px; letter-spacing: 0.3px; }
  .site-nav a { color: var(--ink); text-decoration: none; text-transform: uppercase; }
  .site-nav a.is-active { color: var(--accent); }

  .hero-photo { position: absolute; left: 30px; top: 140px; width: 735px; height: 445px;
    background: radial-gradient(ellipse 60% 55% at 62% 45%, var(--bean-mid) 0%, rgba(122,74,51,0.55) 45%, rgba(255,255,255,0) 100%); }

  .brand { position: absolute; left: 28px; top: 92px; margin: 0; font-weight: 300; font-style: italic; font-size: 46px; line-height: 60px; color: var(--ink); }
  .hours { position: absolute; left: 28px; top: 272px; font-size: 11px; color: var(--accent); line-height: 15px; }
  .hours strong { font-weight: 700; display: block; }
  .hours .days { margin-right: 18px; }

  .welcome { position: absolute; left: 25px; top: 540px; width: 442px; }
  .welcome h2 { margin: 0 0 14px; font-weight: 300; font-size: 25px; color: var(--ink); }
  .welcome p { margin: 0 0 14px; font-size: 11.6px; line-height: 14.6px; color: var(--ink-soft); }
  .guarantee { position: absolute; right: 21px; top: 813px; margin: 0; font-size: 11.6px; font-weight: 700; color: #3e1d14; }

  .clients { position: absolute; left: 0; top: 882px; width: 765px; height: 318px; background: var(--band); }
  .clients h3 { position: absolute; left: 24px; top: 10px; margin: 0; font-weight: 400; font-size: 17px; letter-spacing: 0.4px; color: var(--band-text); text-transform: uppercase; }
  .client { position: absolute; display: flex; align-items: center; justify-content: center; text-align: center; font-size: 7.5px; font-weight: 700; line-height: 9px; color: var(--band-text); }
  .c-green { background: #3d7a2c; }
  .c-light { background: #ece4dc; color: var(--ink); }
  .c-navy { background: #2b2f6e; }
  .c-blue { background: #1f4f8c; }
  .c-teal { background: #2d5a3e; }
  .c-red { background: #8c1f24; }
</style>
</head>
<body>
  <nav class="site-nav">
    <a href="#">Home</a>
    <a href="#">Coffee &amp; Tea</a>
    <a href="#">Condiments</a>
    <a href="#" class="is-active">Paper &amp; Plastics</a>
    <a href="#">Contact</a>
  </nav>

  <div class="hero-photo" role="img" aria-label="Roasted coffee beans scattered on a white background"></div>

  <h1 class="brand">Velmore<br>Brothers<br>Beans</h1>
  <div class="hours">
    <strong>1-800-555-0142</strong>
    <span class="days">MON - FRI</span> 9 - 5 &nbsp;CENTRAL TIME
  </div>

  <section class="welcome">
    <h2>Welcome to Velmore Brothers Beans</h2>
    <p>We are a family-owned and operated business based in Cedar Bend Texas. Since the opening of the Velmore Brothers Beans plant in 1995, we have become Texas' premier independently owned coffee packaging company. Our success relies solely on the principle of selling only the freshest, highest-quality in-room coffee available.</p>
    <p>Velmore Brothers packages and supplies in-room coffee, tea products, and condiments. Whether we're supplying a 50-room Hotel or a 500-room grand resort, we have the distribution capacity to fill your rooms with the most aromatic and robust coffees and teas available at competitive prices.</p>
    <p>Velmore Brothers is continuously striving for ways to improve quality and product appearance to meet the highest standards in today's franchises and independent hotels. We are very aware that our success depends entirely upon maintaining our customers' confidence in our products, so we pay close attention to your needs every step of the way.</p>
  </section>
  <p class="guarantee">We guarantee all of our products will meet your level of satisfaction.</p>

  <section class="clients">
    <h3>Serving fine establishments everywhere !</h3>

    <div class="client c-green" style="left:24px;top:84px;width:58px;height:29px;">Northgate Express</div>
    <div class="client c-light" style="left:94px;top:84px;width:68px;height:29px;">Rowanby</div>
    <div class="client c-navy" style="left:178px;top:82px;width:56px;height:34px;">Harbor Inn</div>

    <div class="client c-blue" style="left:24px;top:144px;width:38px;height:42px;">Cozy Inn</div>
    <div class="client c-navy" style="left:80px;top:144px;width:44px;height:40px;">Restful Inn</div>
    <div class="client c-teal" style="left:138px;top:144px;width:38px;height:42px;">Prime Inn</div>
    <div class="client c-red" style="left:197px;top:142px;width:40px;height:44px;">Clearview Hotel</div>
    <div class="client c-green" style="left:265px;top:144px;width:58px;height:28px;">Northgate Express</div>

    <div class="client c-light" style="left:24px;top:222px;width:66px;height:28px;">Rowanby</div>
    <div class="client c-navy" style="left:108px;top:218px;width:54px;height:34px;">Harbor Inn</div>
    <div class="client c-blue" style="left:203px;top:212px;width:38px;height:42px;">Cozy Inn</div>
    <div class="client c-navy" style="left:259px;top:212px;width:44px;height:40px;">Restful Inn</div>
    <div class="client c-teal" style="left:317px;top:212px;width:38px;height:42px;">Prime Inn</div>
    <div class="client c-red" style="left:375px;top:210px;width:40px;height:44px;">Clearview Hotel</div>
  </section>
</body>
</html>
```